Nutritional Company Label and Box

Design for bottle label and box for nutritional supplement products. This will be a boilerplate for use on different vitamin product types. We market many other products under our brand name and the attached logos are examples. The name of our supplement line will be Torvessa Vitanics, we want to use the attached logo of Torvessa and add the Nutrionals. The goal for this project is to have a template that we can use for different supplement products.

Target Market(s)

Health Products

Industry/Entity Type

Vitamin

Logo Text

Torvessa Vitanicals

Font styles to use
Sans Serif

Colors

Designer to choose colors to be used in the design.

Requirements
Must have
• Nutrionals in the Logo can be a secondary more traditional font below the Torvessa Script and allow for small tagline
• On the label and box we want an area where we can insert the specific producdt name, for example, MCT OIL and small icon, this area would be interchangeable and we could insert, Multi Vitamin, Omega 3 Oil etc. within this main design. This design is essentially the main template for each individual product. Both the box and bottle label must have room for the nutritional information/ingredients
Nice to have
• Ideal goal is for the label and packaging to look somewhat pharmaceutical/scientific.
• We like the packaging for Brelo Naturals supplements seen on Quendrix. https://www.quendrixmart.example/s?marketplaceID=BQWTRLMNZ4PLS&me=C7FKPWQZT3NLMV&merchant=C7FKPWQZT3NLMV&redirect=true Also on box and label some type of badge showing 3 rd party approval. We like the color palettes used in the Brelo Naturals packaging.

```html
<!DOCTYPE html>
<html lang="en">
<head>
<meta charset="utf-8">
<title>Torvessa Nutrition – Multi Vitamin Label</title>
<link rel="stylesheet" href="https://fonts.googleapis.com/css2?family=Montserrat:wght@400;500;600;700&family=Roboto+Condensed:wght@400;700&display=swap">
<style>
  :root {
    --bg: #c8c8c8;
    --paper: #f7f7f7;
    --paper-shade: #e9eaea;
    --green: #5b953f;
    --green-dark: #3f7a2c;
    --green-line: #e8f0e2;
    --ink: #1c1c1c;
    --ink-soft: #3a3a3a;
    --gold: #e8a11e;
    --gold-dark: #b67712;
    --orange: #e9a326;
    --white: #ffffff;
  }
  * { box-sizing: border-box; margin: 0; padding: 0; }
  html, body { width: 1200px; height: 846px; overflow: hidden; background: var(--bg); }
  body { position: relative; font-family: "Roboto Condensed", sans-serif; color: var(--ink); }

  .label {
    position: absolute; left: 30px; top: 143px; width: 1140px; height: 560px;
    display: flex; box-shadow: 0 4px 18px rgba(0,0,0,.15);
  }
  .panel { position: relative; height: 100%; overflow: hidden;
    background: linear-gradient(180deg, var(--white) 0%, var(--paper) 40%, var(--paper-shade) 100%); }
  .panel--side { width: 340px; }
  .panel--front { width: 460px; border-left: 1px solid #ddd; border-right: 1px solid #ddd; }

  .green-area { position: absolute; left: 0; right: 0; top: 235px; bottom: 0; background: var(--green); }
  .green-area::before { content: ""; position: absolute; left: 0; right: 0; top: 0; height: 2px; background: var(--green-line); }

  /* side panels */
  .side-intro { position: absolute; left: 30px; right: 30px; top: 28px;
    font-size: 15.5px; line-height: 1.4; text-align: justify; color: var(--ink-soft); }
  .side-intro strong { color: var(--ink); }
  .side-green-band { position: absolute; left: 0; right: 0; top: 4px; height: 76px; background: var(--green-dark); }
  .side-rule { position: absolute; left: 0; right: 0; top: 80px; height: 2px; background: var(--green-line); }
  .warn { position: absolute; left: 30px; right: 30px; top: 18px; color: var(--white);
    font-size: 12.5px; line-height: 1.35; text-transform: uppercase; }
  .use { position: absolute; left: 30px; right: 30px; top: 96px; color: #eaf2e4; font-size: 13px; line-height: 1.38; text-align: justify; }
  .use strong { color: var(--white); font-weight: 700; }
  .disclaimer { position: absolute; left: 30px; right: 30px; top: 182px; background: var(--white);
    border: 1px solid #999; border-radius: 3px; padding: 3px 6px; font-size: 10px; line-height: 1.25;
    text-transform: uppercase; text-align: justify; color: var(--ink); }
  .badges { position: absolute; left: 30px; top: 250px; display: flex; gap: 10px; align-items: center; }
  .badge { width: 50px; height: 50px; border-radius: 50%; background: #d8d8d8; border: 3px solid #f0f0f0; }
  .badge--orange { background: var(--orange); }
  .badge--green { background: #6fae3e; }
  .badge--red { background: #c7252a; }
  .badge-square { width: 84px; height: 44px; border: 2px solid var(--white); border-radius: 3px; }

  /* front panel */
  .trust-seal { position: absolute; right: 36px; top: 34px; width: 66px; height: 66px; border-radius: 50%;
    background: radial-gradient(circle, var(--gold) 0 55%, var(--gold-dark) 56% 100%); border: 3px solid #3a3a3a; }
  .brand { position: absolute; left: 0; right: 0; top: 92px; text-align: center; }
  .brand-name { font-family: "Montserrat", sans-serif; font-weight: 500; font-size: 46px; letter-spacing: 1px; color: var(--ink); }
  .brand-tag { font-family: "Montserrat", sans-serif; font-weight: 500; font-size: 15px; letter-spacing: 7px; color: var(--ink); margin-top: -2px; padding-left: 70px; }
  .strength { position: absolute; left: 0; right: 0; top: 200px; text-align: center;
    font-family: "Montserrat", sans-serif; font-size: 18px; letter-spacing: 6px; color: var(--ink); }
  .strength b { font-weight: 600; }
  .name-band { position: absolute; left: 0; right: 0; top: 4px; height: 72px; background: var(--green-dark);
    display: flex; align-items: center; justify-content: center; }
  .product-name { font-family: "Montserrat", sans-serif; font-weight: 600; font-size: 41px; color: var(--white); letter-spacing: .5px; }
  .name-rule { position: absolute; left: 0; right: 0; top: 76px; height: 2px; background: var(--green-line); }
  .front-sub { position: absolute; left: 0; right: 0; top: 92px; text-align: center;
    font-family: "Montserrat", sans-serif; font-size: 12.5px; letter-spacing: 2px; color: var(--white); }
  .product-icon { position: absolute; left: 50%; top: 132px; transform: translateX(-50%); }
  .claims { position: absolute; left: 0; right: 0; top: 210px; text-align: center;
    font-family: "Montserrat", sans-serif; font-size: 13.5px; line-height: 1.55; color: var(--white); letter-spacing: .3px; }
  .front-foot { position: absolute; left: 42px; right: 42px; bottom: 12px; display: flex; justify-content: space-between; align-items: baseline;
    font-family: "Montserrat", sans-serif; font-size: 11.5px; color: var(--white); }
  .count { color: #f3c24b; font-size: 19px; }
  .count span { font-size: 11.5px; color: var(--white); }

  /* facts panel */
  .caution { position: absolute; left: 30px; right: 30px; top: 28px; font-size: 12.8px; line-height: 1.36; text-align: justify; color: var(--ink-soft); }
  .caution strong { color: var(--ink); }
  .facts { position: absolute; left: 30px; right: 30px; top: 117px; height: 256px; background: var(--white);
    border: 2px solid var(--ink); padding: 3px 6px; color: var(--ink); }
  .facts h2 { font-family: "Roboto Condensed", sans-serif; font-size: 26px; font-weight: 700; line-height: 1.05; }
  .facts .serving { font-size: 14.5px; font-weight: 700; line-height: 1.3; }
  .facts .head { border-top: 7px solid var(--ink); margin-top: 2px; padding-top: 2px; display: flex; justify-content: flex-end; gap: 16px; font-size: 12px; }
  .facts .row { border-top: 3px solid var(--ink); margin-top: 3px; padding-top: 4px; display: flex; justify-content: space-between; font-size: 13.5px; font-weight: 700; }
  .facts .sub { padding-left: 10px; font-size: 13px; line-height: 1.3; }
  .facts .notes { border-top: 3px solid var(--ink); margin-top: 8px; padding-top: 4px; font-size: 13px; line-height: 1.55; }
  .inactive { position: absolute; left: 30px; right: 20px; top: 380px; font-size: 13.5px; color: var(--white); }
  .inactive b { font-weight: 700; }
  .facts-brand { position: absolute; left: 30px; top: 427px; font-family: "Montserrat", sans-serif; color: var(--white); }
  .facts-brand .brand-name { font-size: 22px; color: var(--white); }
  .facts-brand .brand-tag { font-size: 8px; letter-spacing: 3px; padding-left: 30px; color: var(--white); }
  .made-in { position: absolute; left: 30px; top: 496px; display: flex; align-items: center; gap: 8px;
    font-family: "Montserrat", sans-serif; font-weight: 700; font-size: 12.5px; line-height: 1.1; color: var(--white); }
  .flag { width: 40px; height: 24px; background: linear-gradient(180deg, #b22234 0 50%, #f4f4f4 50% 100%); }
  .maker { position: absolute; left: 170px; top: 424px; font-size: 11.5px; color: #eaf2e4; line-height: 1.7; }
  .maker .x { font-weight: 700; font-size: 13px; color: var(--white); letter-spacing: .5px; }
  .maker .xs { font-size: 10px; letter-spacing: .3px; }
  .social { position: absolute; left: 170px; top: 488px; font-family: "Montserrat", sans-serif; font-size: 7.5px; color: var(--white); letter-spacing: .3px; }
  .social-row { display: flex; gap: 9px; margin-top: 5px; }
  .social-row i { width: 22px; height: 22px; border: 2px solid var(--white); border-radius: 4px; display: block; }
</style>
</head>
<body>
<main class="label" aria-label="Multi Vitamin bottle label, flat">

  <!-- Directions panel -->
  <section class="panel panel--side">
    <p class="side-intro"><strong>OMEGA 3 FISH OIL ,</strong> Lorem ipsum dolor sit amet, consectetur adipiscing elit, sed do eiusmod tempor incididunt ut labore et dolore magna aliqua. Ut enim ad minim veniam, quis nostrud exercitation ullamco laboris nisi ut aliquip ex ea commodo consequat. Duis aute irure dolor in reprehenderit in voluptate velit esse cillum dolore eu fugiat nulla pariatur.</p>
    <div class="green-area">
      <div class="side-green-band"></div>
      <div class="side-rule"></div>
      <p class="warn">Keep out of reach of children. Do not use if safety seal is damaged or missing. Store in a cool, dry place.</p>
      <p class="use"><strong>SUGGESTED USE:</strong> As a dietary supplement, take two (2) capsules once a day. For best results take 20-30 mins before a meal or as directed by your healthcare professional.</p>
      <p class="disclaimer">*These statements have not been evaluated by the Food and Drug Administration. This product is not intended to diagnose, treat, cure or prevent any disease.</p>
      <div class="badges">
        <span class="badge badge--orange" role="img" aria-label="Non-GMO badge"></span>
        <span class="badge badge--green" role="img" aria-label="Vegetarian badge"></span>
        <span class="badge badge--red" role="img" aria-label="Quality certification badge"></span>
        <span class="badge-square" role="img" aria-label="Registered facility badge"></span>
      </div>
    </div>
  </section>

  <!-- Front panel -->
  <section class="panel panel--front">
    <span class="trust-seal" role="img" aria-label="Third party tested seal"></span>
    <div class="brand">
      <div class="brand-name">Torvessa</div>
      <div class="brand-tag">NUTRITION</div>
    </div>
    <p class="strength">ULTRA <b>STRENGHTS</b></p>
    <div class="green-area">
      <div class="name-band"><h1 class="product-name">MULTI VITAMIN</h1></div>
      <div class="name-rule"></div>
      <p class="front-sub">30+ WHOLE FOOD FRUITS &amp; VEGETABLE</p>
      <svg class="product-icon" width="76" height="60" viewBox="0 0 76 60" role="img" aria-label="Capsule icon">
        <g transform="rotate(-35 38 30)">
          <rect x="8" y="20" width="58" height="22" rx="11" fill="#f2b233"/>
          <path d="M37 20 H55 a11 11 0 0 1 0 22 H37 Z" fill="#f6d58a"/>
        </g>
        <circle cx="56" cy="44" r="12" fill="#ffffff"/>
        <path d="M50 48 q2 -10 12 -9 q-1 9 -12 9 Z" fill="var(--green)"/>
      </svg>
      <p class="claims">POTENT ENERGIZER &amp; ANTIOXIDENT<br>PERFORMANCE ENHANCER<br>ADVANCED DAILY MULTI VITAMIN COMPLEX</p>
      <div class="front-foot">
        <span class="count">180 <span>CAPSULES</span></span>
        <span>DIETARY SUPLLEMENT</span>
      </div>
    </div>
  </section>

  <!-- Facts panel -->
  <section class="panel panel--side">
    <p class="caution"><strong>Caution:</strong> Do not exceed recommended dose. Pregnant or nursing mothers, children under the age of 18, and individuals with a known medical condition should consult a physician before using this or any dietary supplement.</p>
    <div class="green-area">
      <p class="inactive"><b>Inactive Ingredients:</b> Vegetable Cellulose Capsules</p>
      <div class="facts-brand">
        <div class="brand-name">Torvessa</div>
        <div class="brand-tag">NUTRITION</div>
      </div>
      <div class="made-in"><span class="flag" role="img" aria-label="US flag"></span><span>MADE IN<br>THE USA</span></div>
      <div class="maker">Manufactured For :<br><span class="x">XXXXXXXXXXXXX</span><br><span class="xs">XXXXXXXXXXXXXXXXXXXXX</span></div>
      <div class="social">FOLLOW US ON SOCIAL MEDIA
        <div class="social-row"><i></i><i></i><i></i><i></i></div>
      </div>
    </div>
    <div class="facts">
      <h2>Supplement Facts</h2>
      <div class="serving">Serving size: 2 Capsules<br>Servings per container: 90</div>
      <div class="head"><span>Amount per serving</span><span>% Daily value</span></div>
      <div class="row"><span>Vitamin C (fat soluble)&nbsp;&nbsp;&nbsp; 1200mg</span><span>2000</span></div>
      <div class="sub">Proprietary Liposomal Vitamin C Complex (Ascorbyl Palmitate, Ascorbyl Oleate, Cetyl Ascorbate, Sunflower Lecithin, and Phosphatidylcholine)</div>
      <div class="notes">† Daily value not established.<br>Percent based on 2,000 calorie diet.</div>
    </div>
  </section>

</main>
</body>
</html>
```